Hartwell Estates Business Cards

I would like a business card that includes myself and my partner.
Includes: Logo, office #, email, website, our names, our numbers and possibly the address. I would also like the logo to be embossed and the card to be horizontal.
There is a photo of our yard signs to give you an idea of the colors of our business.

Target Market(s)

Everyone in real estate market.
We are in a rural area. Our clientele are from all socioeconomic backgrounds.

Industry/Entity Type

Real Estate Agent

Contact Information for Business Card

Company Name: Hartwell Estates
Our Names, Titles & Cell #'s : Dana Pembrook-Broker (555).317.6624, Marla Pembrook-Realtor (555).609.1385
Office #: (555).240.3918
Website: hartwellestates-demo.com
Joint Email: pembrook@hartwellestates-demo.com
Office Address: 418B W. Calloway Ave.
Millbrook, LA. 70913

Font styles to use
Serif

Requirements
Must have
• HORIZONTAL, Logo, Myself and my partners names, Our cell #'s, our office #, our website, our email address
Nice to have
• Embossed logo, office address, our titles.

```html
<!DOCTYPE html>
<html lang="en">
<head>
<meta charset="utf-8">
<title>Hartwell Estates Business Cards</title>
<link href="https://fonts.googleapis.com/css2?family=Open+Sans:wght@400;600;700&display=swap" rel="stylesheet">
<style>
  :root {
    --backdrop: #7a6448;
    --paper: #ffffff;
    --paper-shade: #ececec;
    --purple: #4e2a6e;
    --purple-deep: #3a1c57;
    --purple-light: #6a3d8f;
    --ink-light: #ffffff;
    --ink-soft: #e6dcef;
  }
  * { box-sizing: border-box; margin: 0; padding: 0; }
  html, body { width: 1200px; height: 843px; overflow: hidden; }
  body {
    background: var(--backdrop);
    font-family: "Open Sans", Arial, sans-serif;
    display: flex;
    align-items: center;
    justify-content: center;
    gap: 40px;
  }
  .card {
    width: 540px;
    height: 309px;
    border-radius: 4px;
    position: relative;
    box-shadow: 0 10px 28px rgba(0,0,0,0.35);
    overflow: hidden;
  }
  /* Front */
  .card-front {
    background: linear-gradient(160deg, var(--paper) 55%, var(--paper-shade));
    display: flex;
    align-items: center;
    justify-content: center;
  }
  .brand {
    display: flex;
    align-items: center;
    gap: 16px;
    color: var(--purple);
  }
  .brand-dot {
    width: 44px; height: 44px;
    border-radius: 50%;
    background: var(--purple);
    flex: none;
  }
  .brand-name {
    font-weight: 700;
    font-size: 36px;
    letter-spacing: 0.5px;
  }
  /* Back */
  .card-back {
    background: linear-gradient(120deg, var(--purple-light) 0%, var(--purple) 45%, var(--purple-deep) 100%);
    color: var(--ink-light);
    padding: 26px 28px;
  }
  .contact { width: 270px; }
  .person-name { font-weight: 600; font-size: 17px; line-height: 1.2; }
  .person-title, .person-phone { font-size: 12px; line-height: 1.35; color: var(--ink-soft); }
  .person + .person { margin-top: 6px; }
  .office-address { margin-top: 16px; font-size: 12.5px; line-height: 1.4; color: var(--ink-soft); }
  .office-lines { margin-top: 6px; list-style: none; font-size: 12.5px; line-height: 1.5; color: var(--ink-soft); }
  .office-lines li { display: flex; align-items: center; gap: 7px; white-space: nowrap; }
  .office-lines svg { width: 11px; height: 11px; flex: none; }
  .brand-mark {
    position: absolute;
    right: 30px;
    top: 50%;
    transform: translateY(-50%);
    width: 200px;
    display: flex;
    flex-direction: column;
    align-items: center;
    gap: 14px;
    color: var(--ink-light);
  }
  .brand-mark .brand-ring {
    width: 80px; height: 80px;
    border-radius: 50%;
    background: var(--ink-light);
  }
  .brand-mark .brand-name {
    font-size: 34px;
    text-align: center;
    line-height: 1.1;
  }
</style>
</head>
<body>
  <section class="card card-front" aria-label="Card front">
    <div class="brand">
      <span class="brand-dot"></span>
      <span class="brand-name">Hartwell Estates</span>
    </div>
  </section>

  <section class="card card-back" aria-label="Card back">
    <div class="contact">
      <div class="person">
        <p class="person-name">Dana Pembrook</p>
        <p class="person-title">Broker</p>
        <p class="person-phone">(555).317.6624</p>
      </div>
      <div class="person">
        <p class="person-name">Marla Pembrook</p>
        <p class="person-title">Realtor</p>
        <p class="person-phone">(555).609.1385</p>
      </div>
      <p class="office-address">418B W. Calloway Ave.<br>Millbrook, LA. 70913</p>
      <ul class="office-lines">
        <li>
          <svg viewBox="0 0 24 24" aria-hidden="true"><path fill="currentColor" d="M6.6 10.8a15.1 15.1 0 0 0 6.6 6.6l2.2-2.2a1 1 0 0 1 1-.25 11.4 11.4 0 0 0 3.6.57 1 1 0 0 1 1 1V20a1 1 0 0 1-1 1A17 17 0 0 1 3 4a1 1 0 0 1 1-1h3.5a1 1 0 0 1 1 1c0 1.25.2 2.45.57 3.57a1 1 0 0 1-.25 1z"/></svg>
          (555).240.3918
        </li>
        <li>
          <svg viewBox="0 0 24 24" aria-hidden="true"><path fill="currentColor" d="M2 5h20v14H2zm2 2v.5l8 5 8-5V7z"/></svg>
          pembrook@hartwellestates-demo.com
        </li>
        <li>
          <svg viewBox="0 0 24 24" aria-hidden="true"><circle cx="12" cy="12" r="9" fill="none" stroke="currentColor" stroke-width="2"/><path d="M3 12h18M12 3c3 3 3 15 0 18M12 3c-3 3-3 15 0 18" fill="none" stroke="currentColor" stroke-width="1.6"/></svg>
          hartwellestates-demo.com
        </li>
      </ul>
    </div>
    <div class="brand-mark">
      <span class="brand-ring"></span>
      <span class="brand-name">Hartwell Estates</span>
    </div>
  </section>
</body>
</html>
```